Diverse, up-scale salon needs eye-catching, unique business cards.

We are looking for a unique business card design for our stylist but that can also be multi functional and used for appointment reminder and referrals. I will need a design in a format that I can modify names and titles going forward. In the past we have had a dark background with the logo on one side, and stylist and contact information on the other but we are open to all ideas. I have included our mission statement as well as branded colors below. The statement doesn't need to go on the card, it's just a reference for target market. We need space for the stylists name, title, instagram handle and then the salons phone number, website and address. I am also open to adding a spot for a qr code linked to the stylist instagram or the salon booking link.

primary brand colors:
#333333 #233415 #36502a #93874a #000000
Mission statement:
Vessolin Hair Studio, a high-end salon located in the lively Downtown Farmington, Michigan, is committed to providing exceptional services in a welcoming and relaxed environment to meet the needs of our diverse clientele.
Our salon specializes in contemporary custom haircuts, coloring, extensions, and barbering and beard grooming services. Our team of skilled stylists is passionate and inventive in their hair styling techniques. At the heart of our salon are values centered on quality, innovation, creativity, and above all, comfort. These core values are evident in every appointment across our customizable array of services.
Our goal is to establish a benchmark for exceptional hair care for every human.
Website: www.vessolinhairstudio.example
instagram: @vessolinhairstudio
address: 41782 Pelham Crest Rd, Farmington MI
phone: 248-613-4087

Industry/Entity Type

Hair Salon

Contact Information for Business Card

Stylist name, title, phone, instagram, website, address, (optional qr code)

Requirements
Should not have
• Does not need mission statement on the card.

```html
<!DOCTYPE html>
<html lang="en">
<head>
<meta charset="utf-8">
<title>Vessolin Hair Studio — Business Card</title>
<link rel="stylesheet" href="https://fonts.googleapis.com/css2?family=Montserrat:wght@400;500;700&display=swap">
<style>
  :root {
    --backdrop: #3a3a3a;
    --card: #161616;
    --gold: #93874a;
    --ink-light: #f2f2f2;
  }
  html, body {
    margin: 0;
    padding: 0;
    width: 1200px;
    height: 1059px;
    overflow: hidden;
    background: var(--backdrop);
    font-family: "Montserrat", sans-serif;
  }
  .canvas {
    position: relative;
    width: 1200px;
    height: 1059px;
  }
  .card {
    position: absolute;
    background: var(--card);
    box-shadow: 0 10px 24px rgba(0,0,0,0.55);
  }
  .card--front { left: 256px; top: 100px; width: 688px; height: 390px; }
  .card--back  { left: 253px; top: 537px; width: 694px; height: 394px; }

  .brand-mark {
    position: absolute;
    display: flex;
    flex-direction: column;
    align-items: center;
    transform: translateX(-50%);
  }
  .brand-mark__circle {
    border: 3px solid var(--gold);
    border-radius: 50%;
    box-sizing: border-box;
  }
  .brand-mark__name {
    color: var(--gold);
    font-weight: 700;
    letter-spacing: 0.12em;
    white-space: nowrap;
    margin-top: 18px;
  }
  .card--front .brand-mark { left: 194px; top: 120px; }
  .card--front .brand-mark__circle { width: 92px; height: 92px; }
  .card--front .brand-mark__name { font-size: 16px; }
  .card--back .brand-mark { left: 347px; top: 108px; }
  .card--back .brand-mark__circle { width: 132px; height: 132px; }
  .card--back .brand-mark__name { font-size: 24px; margin-top: 24px; }

  .divider {
    position: absolute;
    left: 344px;
    top: 90px;
    width: 2px;
    height: 210px;
    background: var(--gold);
  }
  .details {
    position: absolute;
    left: 382px;
    top: 84px;
    color: var(--ink-light);
  }
  .details__name {
    margin: 0;
    color: var(--gold);
    font-size: 28px;
    font-weight: 700;
    letter-spacing: 0.04em;
    line-height: 1;
  }
  .details__title {
    margin: 9px 0 0;
    font-size: 16px;
    font-weight: 500;
    letter-spacing: 0.06em;
  }
  .details__address {
    margin: 20px 0 0;
    font-size: 16px;
    line-height: 20px;
    font-style: normal;
  }
  .contact-list {
    list-style: none;
    margin: 16px 0 0;
    padding: 0;
    font-size: 16px;
  }
  .contact-list li {
    display: flex;
    align-items: center;
    height: 22.5px;
  }
  .contact-list svg {
    width: 13px;
    height: 13px;
    margin-right: 8px;
    flex: none;
  }
</style>
</head>
<body>
<div class="canvas">

  <section class="card card--front">
    <div class="brand-mark">
      <div class="brand-mark__circle"></div>
      <div class="brand-mark__name">VESSOLIN HAIR STUDIO</div>
    </div>

    <div class="divider"></div>

    <div class="details">
      <h1 class="details__name">DORIAN KESSLER</h1>
      <p class="details__title">MANAGER</p>
      <address class="details__address">41782 Pelham Crest<br>Rd, Farmington MI</address>
      <ul class="contact-list">
        <li>
          <svg viewBox="0 0 16 16" aria-hidden="true"><path fill="#93874a" d="M3.5 1.5l2.5 0 1 3.5-1.8 1.2a8 8 0 0 0 4.6 4.6L11 9l3.5 1v2.5c0 1-1 2-2 2A11 11 0 0 1 1.5 3.5c0-1 1-2 2-2z"/></svg>
          248-613-4087
        </li>
        <li>
          <svg viewBox="0 0 16 16" aria-hidden="true"><rect x="1" y="3" width="14" height="10" rx="1" fill="#93874a"/><path d="M1.5 4l6.5 5 6.5-5" fill="none" stroke="#161616" stroke-width="1.3"/></svg>
          info@vessolinhairstudio.example
        </li>
        <li>
          <svg viewBox="0 0 16 16" aria-hidden="true"><g fill="none" stroke="#93874a" stroke-width="1.2"><circle cx="8" cy="8" r="6.5"/><ellipse cx="8" cy="8" rx="3" ry="6.5"/><path d="M1.5 8h13M2.5 5h11M2.5 11h11"/></g></svg>
          www.vessolinhairstudio.example
        </li>
        <li>
          <svg viewBox="0 0 16 16" aria-hidden="true"><circle cx="8" cy="8" r="6" fill="none" stroke="#93874a" stroke-width="1.4"/></svg>
          @vessolinhairstudio
        </li>
      </ul>
    </div>
  </section>

  <section class="card card--back">
    <div class="brand-mark">
      <div class="brand-mark__circle"></div>
      <div class="brand-mark__name">VESSOLIN HAIR STUDIO</div>
    </div>
  </section>

</div>
</body>
</html>
```